Sleek wordpress site for Bramblecrest finishing works

We are a commercial job shop that serves B2B, govt & LEO and retail clients.We need a wordpress site with 6 individual pages: homepage, coating, laser engraving, laser cutting, part marking, and contact us. I have attached an outline of the desired flow and sub headings for each page. I would like to incorporate the colors of the logo through out the site to be clean and sleek enough to appeal to B2B commercial clients yet be inviting enough for retail clients.

I would like to have easy picture functionality so photographs on each page can be updated easily.

Target Market(s)

B2B industrial & Govt and Military part marking, laser engraving and coating: machine shops, aerospace companies, tool manufactures. Retail: personalized gifts, Job Shop

Coding

Coded - Design and coding required

Font styles to use
Sans Serif
Other font styles liked:
• Open to suggestion

Colors
0255a3
3176b5
eaf1f7
cfdeed
ffffff

Requirements
Must have
• Clean easy to navigate flow, separate pages as indicated on attached outline, high class feel. Great picture functionality, professional and inviting feel,
• **update: needs to be optimized for mobile, should have a gallery function. Gallery can be an additional page or embedded
Nice to have
• Social media connectivity links,
Should not have
• crappy plugins that make back-end management difficult, no blog

```html
<!DOCTYPE html>
<html lang="en">
<head>
<meta charset="utf-8">
<title>Bramblecrest Finishing Works</title>
<link rel="stylesheet" href="https://fonts.googleapis.com/css2?family=Open+Sans:wght@400;600;700&display=swap">
<style>
:root{
  --brand:#0255a3;
  --brand-mid:#3176b5;
  --brand-pale:#eaf1f7;
  --brand-soft:#cfdeed;
  --white:#ffffff;
  --ink:#555a60;
  --line:#d9d9d9;
  --panel:#f4f4f4;
}
*{box-sizing:border-box;margin:0;padding:0}
html,body{width:1200px;height:2344px;overflow:hidden}
body{font-family:"Open Sans",Arial,sans-serif;background:var(--white);position:relative;color:var(--ink)}
.hero{position:absolute;left:0;top:0;width:1200px;height:645px;
  background:radial-gradient(ellipse at 45% 25%,#6a5238 0%,#3a2d22 35%,#1c1814 65%,#0c0b0a 100%)}
.brand{position:absolute;left:78px;top:54px;display:flex;align-items:center;gap:12px;
  color:var(--white);font-weight:700;font-size:22px;letter-spacing:.5px;text-transform:uppercase;line-height:1.1}
.brand-dot{width:30px;height:30px;border-radius:50%;background:var(--white);flex:none}
.main-nav{position:absolute;right:80px;top:58px;display:flex;gap:26px}
.main-nav a{color:var(--white);text-decoration:none;font-size:15px;text-transform:uppercase;padding-top:12px;position:relative}
.main-nav a.is-active::before{content:"";position:absolute;left:-2px;right:-2px;top:0;height:1px;background:var(--white)}
.hero-title{position:absolute;left:0;width:1200px;top:292px;text-align:center;color:var(--white);
  font-size:44px;font-weight:700;letter-spacing:-.3px;text-shadow:0 2px 6px rgba(0,0,0,.6)}
.hero-tags{position:absolute;left:0;width:1200px;top:368px;display:flex;justify-content:center;gap:48px;
  color:var(--white);font-size:23px;font-weight:700;text-shadow:0 2px 4px rgba(0,0,0,.6)}
.section-title{position:absolute;left:0;width:1200px;top:696px;text-align:center;color:var(--brand);font-size:37px;font-weight:700}
.service-card{position:absolute;width:500px;height:218px;border:1.5px solid var(--line);border-radius:8px;background:var(--white);text-align:center}
.service-icon{position:absolute;left:197px;top:-52px;width:105px;height:105px;border-radius:50%;background:var(--brand);
  display:flex;align-items:center;justify-content:center}
.service-name{margin-top:68px;color:var(--brand);font-size:26px;font-weight:700;line-height:36px}
.service-text{margin:10px auto 0;width:466px;font-size:14px;line-height:25px;letter-spacing:-.15px;color:var(--ink)}
.service-text a{color:var(--brand);font-weight:700;text-decoration:underline}
.newsletter{position:absolute;left:0;top:1469px;width:1200px;height:165px;
  background:linear-gradient(100deg,#2d2d2f 0%,#4a4a4d 40%,#262628 70%,#3c3c3e 100%)}
.newsletter-panel{position:absolute;left:0;top:0;width:1200px;height:165px}
.newsletter-title{position:absolute;left:80px;top:40px;color:var(--white);font-size:37px;font-weight:700}
.newsletter-sub{position:absolute;left:80px;top:98px;color:var(--white);font-size:15px}
.newsletter-form{position:absolute;left:634px;top:65px;display:flex;height:50px}
.newsletter-input{width:355px;background:var(--white);font-size:15px;color:#666;padding:14px 22px}
.newsletter-btn{width:133px;background:var(--brand);color:var(--white);font-size:21px;font-weight:700;display:flex;align-items:center;justify-content:center}
.contact-photo{position:absolute;left:0;top:1967px;width:1200px;height:314px;
  background:radial-gradient(ellipse at 60% 60%,#3e5552 0%,#2a2a25 40%,#17130f 75%,#0d0b09 100%)}
.contact-card{position:absolute;left:78px;top:1730px;width:1044px;height:320px;background:var(--panel);border-radius:10px}
.field{position:absolute;border-bottom:1px solid var(--line);font-size:15px;color:#666;padding:0 0 12px 22px}
.send-btn{position:absolute;left:442px;top:220px;width:157px;height:41px;background:var(--brand);color:var(--white);
  font-size:18px;font-weight:700;display:flex;align-items:center;justify-content:center;border-radius:2px}
.site-footer{position:absolute;left:0;top:2281px;width:1200px;height:63px;background:var(--brand);color:var(--white);
  font-size:15px;display:flex;align-items:center;justify-content:center}
</style>
</head>
<body>
<header class="hero" role="img" aria-label="Photo of a laser cutting metal sheet with sparks flying">
  <div class="brand"><span class="brand-dot"></span><span>Bramblecrest<br>Finishing Works</span></div>
  <nav class="main-nav">
    <a class="is-active">Home</a><a>Coating</a><a>Laser Engraving</a><a>Laser Cutting</a><a>Part Making</a><a>Contact</a>
  </nav>
  <h1 class="hero-title">BRAMBLECREST FINISHING WORKS</h1>
  <div class="hero-tags"><span>COATING</span><span>|</span><span>PART MARKING</span><span>|</span><span>ENGRAVING</span></div>
</header>

<h2 class="section-title">OUR SERVICES</h2>

<article class="service-card" style="left:78px;top:830px">
  <div class="service-icon"><svg width="50" height="50" viewBox="0 0 50 50" fill="none" stroke="#fff" stroke-width="2"><path d="M12 38l3-10 20-20 7 7-20 20z"/><path d="M15 28l7 7M31 12l7 7"/></svg></div>
  <h3 class="service-name">Part Marking</h3>
  <p class="service-text">Capabilities - Barcodes, 2d Data Matrix, UID Marking, Name plates id tags Asset locator tags... <a>READ MORE</a></p>
</article>

<article class="service-card" style="left:623px;top:830px">
  <div class="service-icon"><svg width="50" height="50" viewBox="0 0 50 50" fill="none" stroke="#fff" stroke-width="2"><path d="M17 8h16v8H17zM21 16l4 8 4-8"/><path d="M25 24v8M20 30l5 3 5-3"/><path d="M9 36h32M12 41h26"/></svg></div>
  <h3 class="service-name">Laser engraving</h3>
  <p class="service-text">What is Duraglaze - Duraglaze is a spray on ceramic based finish that can be applied to metals, plastics, polymers... <a>READ MORE</a></p>
</article>

<article class="service-card" style="left:78px;top:1152px">
  <div class="service-icon"><svg width="54" height="50" viewBox="0 0 54 50" fill="none" stroke="#fff" stroke-width="2"><path d="M27 10l20 9-20 9-20-9z"/><path d="M7 25l20 9 20-9M7 31l20 9 20-9"/></svg></div>
  <h3 class="service-name">Coatings</h3>
  <p class="service-text">Capabilities Statement: With our selection of CO2 and fiber lasers there are very few materials and substrates...<a style="font-weight:400">READ MORE</a></p>
</article>

<article class="service-card" style="left:623px;top:1152px">
  <div class="service-icon"><svg width="50" height="50" viewBox="0 0 50 50" fill="none" stroke="#fff" stroke-width="2"><path d="M19 6v18M25 6v22M31 6v18"/><path d="M14 26l11 10 11-10M25 36l-9 6M25 36l9 6M10 42h30"/></svg></div>
  <h3 class="service-name">Laser Cutting</h3>
  <p class="service-text">What is laser cutting: Laser cutting is a non-contact cutting process with a kurff width of 0.010"... <a>READ MORE</a></p>
</article>

<section class="newsletter" role="img" aria-label="Photo of an engraved dark metal part">
  <svg class="newsletter-panel" viewBox="0 0 1200 165" preserveAspectRatio="none"><polygon points="0,0 574,0 500,165 0,165" fill="#0255a3"/></svg>
  <h2 class="newsletter-title">NEWSLETTER</h2>
  <p class="newsletter-sub">Sign up for our newsletter and follow us on social media</p>
  <div class="newsletter-form"><div class="newsletter-input">Enter Email address</div><div class="newsletter-btn">SUBSCRIBE</div></div>
</section>

<div class="contact-photo" role="img" aria-label="Photo of a laser head cutting a metal plate with sparks"></div>

<form class="contact-card">
  <div class="field" style="left:25px;top:60px;width:303px">Your Name</div>
  <div class="field" style="left:370px;top:60px;width:302px">Your Email</div>
  <div class="field" style="left:714px;top:60px;width:302px">Your phone no.</div>
  <div class="field" style="left:25px;top:143px;width:991px">Your Message</div>
  <div class="send-btn">SEND</div>
</form>

<footer class="site-footer">©BRAMBLECREST FINISHING WORKS. 2018 - All Rights Reserved.</footer>
</body>
</html>
```